Business Card Design for The Lending Nest Inc.

We need a business card design for our mortgage company: "The Lending Nest Inc."

Need to have Social Media Account on there as a possibility

```html
<!DOCTYPE html>
<html lang="en">
<head>
<meta charset="UTF-8">
<title>The Lending Nest Inc. — Business Card</title>
<link rel="stylesheet" href="https://fonts.googleapis.com/css2?family=Montserrat:wght@500;600;700&family=Open+Sans:wght@400&display=swap">
<style>
  :root {
    --page: #ffffff;
    --brand-blue: #1a5fb4;
    --accent-plum: #9b2f6e;
    --ink: #1f1f24;
    --panel: #f7eef0;
    --paint-red: #e0281f;
    --paint-crimson: #b3172a;
    --paint-magenta: #a8317f;
    --paint-violet: #5d3f8f;
    --paint-blue: #6f8fc4;
    --paint-sky: #c9d9ea;
    --paint-orange: #e8641f;
    --white: #ffffff;
  }
  * { box-sizing: border-box; margin: 0; padding: 0; }
  html, body {
    width: 1200px; height: 1200px; overflow: hidden;
    background: var(--page);
  }
  .sheet { position: relative; width: 1200px; height: 1200px; }

  .card {
    position: absolute; left: 188px; width: 888px; height: 528px; overflow: hidden;
  }
  .card--back { top: 72px; }
  .card--front { top: 640px; left: 174px; }

  .paint-texture {
    position: absolute; inset: 0;
    background:
      radial-gradient(ellipse 40% 55% at 8% 75%, var(--paint-sky) 0%, transparent 70%),
      radial-gradient(ellipse 35% 45% at 5% 20%, var(--paint-violet) 0%, transparent 75%),
      radial-gradient(ellipse 40% 50% at 25% 40%, var(--paint-magenta) 0%, transparent 75%),
      radial-gradient(ellipse 25% 25% at 95% 5%, var(--paint-blue) 0%, transparent 70%),
      radial-gradient(ellipse 35% 30% at 80% 15%, var(--paint-orange) 0%, transparent 70%),
      radial-gradient(ellipse 30% 25% at 45% 5%, #3a2430 0%, transparent 70%),
      linear-gradient(120deg, var(--paint-crimson) 0%, var(--paint-red) 55%, var(--paint-red) 100%);
  }

  .panel {
    position: absolute; left: 40px; top: 40px; width: 808px; height: 448px;
    background: linear-gradient(160deg, #f4f1f6 0%, var(--panel) 60%, #fbe9ea 100%);
    text-align: center; font-family: "Montserrat", sans-serif; color: var(--ink);
  }

  .brand {
    position: absolute; left: 0; right: 0;
    display: flex; align-items: center; justify-content: center; gap: 12px;
  }
  .brand__dot {
    width: 34px; height: 34px; border-radius: 50%; background: var(--brand-blue);
  }
  .brand__name {
    font-family: "Montserrat", sans-serif; font-weight: 600; color: var(--brand-blue);
    font-size: 30px; letter-spacing: 0.2px; line-height: 1.2;
  }
  .panel .brand { top: 64px; }

  .holder-title {
    position: absolute; top: 146px; left: 0; right: 0;
    font-weight: 500; font-size: 20px; letter-spacing: 4px; color: var(--accent-plum);
  }
  .rule {
    position: absolute; left: 50%; width: 148px; height: 1px; transform: translateX(-50%);
  }
  .panel .rule { top: 194px; background: var(--ink); }

  .contact {
    position: absolute; left: 0; right: 0;
    font-weight: 700; font-size: 13.5px; letter-spacing: 2.7px;
  }
  .contact--phone { top: 234px; }
  .contact--address { top: 262px; }

  .socials {
    position: absolute; top: 324px; left: 0; right: 0;
  }
  .social {
    position: absolute; top: 0; width: 200px; transform: translateX(-50%);
    display: flex; flex-direction: column; align-items: center; gap: 10px;
  }
  .social:nth-child(1) { left: 214px; }
  .social:nth-child(2) { left: 406px; }
  .social:nth-child(3) { left: 592px; }
  .social__dot {
    width: 36px; height: 36px; border-radius: 50%;
    background: radial-gradient(circle at 35% 35%, var(--accent-plum), var(--paint-red));
  }
  .social__handle { font-weight: 700; font-size: 14px; letter-spacing: 2.6px; }

  .frame {
    position: absolute; left: 40px; top: 42px; width: 806px; height: 446px;
    border: 1.5px solid var(--white); text-align: center;
  }
  .frame .brand { top: 78px; }
  .frame .brand__name { font-size: 40px; }
  .frame .brand__dot { width: 48px; height: 48px; }
  .holder-name {
    position: absolute; top: 176px; left: 0; right: 0;
    font-family: "Open Sans", sans-serif; font-weight: 400; font-size: 58px; line-height: 80px;
    color: var(--white); letter-spacing: 0.5px;
  }
  .frame .rule { top: 292px; background: var(--white); opacity: 0.85; }
  .website {
    position: absolute; top: 326px; left: 0; right: 0;
    font-family: "Open Sans", sans-serif; font-size: 13px; letter-spacing: 3px; color: var(--white);
  }
</style>
</head>
<body>
<main class="sheet">
  <section class="card card--back">
    <div class="paint-texture" role="img" aria-label="Splattered watercolour paint texture in red, magenta, violet and pale blue"></div>
    <div class="panel">
      <div class="brand">
        <span class="brand__dot"></span>
        <span class="brand__name">The Lending Nest Inc.</span>
      </div>
      <p class="holder-title">YOUR NAME</p>
      <div class="rule"></div>
      <p class="contact contact--phone">PHONE: +91 1234567890</p>
      <p class="contact contact--address">45 MAIN ROAD, NEW CITY, YOUR ADDRESS KUSA56A</p>
      <div class="socials">
        <div class="social"><span class="social__dot"></span><span class="social__handle">/CHATTERLY</span></div>
        <div class="social"><span class="social__dot"></span><span class="social__handle">/CHIRPLINE</span></div>
        <div class="social"><span class="social__dot"></span><span class="social__handle">/SNAPFRAME</span></div>
      </div>
    </div>
  </section>

  <section class="card card--front">
    <div class="paint-texture" role="img" aria-label="Splattered watercolour paint texture in red, magenta, violet and pale blue"></div>
    <div class="frame">
      <div class="brand">
        <span class="brand__dot"></span>
        <span class="brand__name">The Lending Nest Inc.</span>
      </div>
      <p class="holder-name">your name</p>
      <div class="rule"></div>
      <p class="website">WWW.YOURSITE.COM</p>
    </div>
  </section>
</main>
</body>
</html>
```